So the ones in the picture are my original cards that I came up with. 😅however I kinda messed up on two things, I missed spelled my name it should be Marcello Vandora as well as the email should be Marcellov@brightlanecrews.com. I would like to clean this card up and also make it pop! Something that people would remember me by and that screams DEMOLITION. As well as a card that give you a feeling of loyalty and trust. I would also like to change and remove junk hauling and add full demolition to replace it. These cards worked for a little while but I cant make that my image while handing these out. I would also like to only put down that we are located in Cedar Ridge Valley, CA, 90000 instead of the address on the card. Also if we can have a line that states Licensed, Bonded, & Insured. With out License # 4837215

Target Market(s)

Contractors and Home owners

Industry/Entity Type

Construction specialist in Demolition

Contact Information for Business Card

R Wrecking Selective Demolition & Full Demolition Kitchens AD Preparation Bathrooms Sheds Interiors & Exteriors Demo Digging And Much More Marcello Vandora Owner our city state and zip

Font styles to use
Serif
Sans Serif
Decorative

Colors
0054AA
0677BA
7BADD7
CADEEF
E8F1F8
0094D4
00A9DD
6FCCEA
C7EBF8
E9F6FB

Requirements
Must have
• License# 4837215
Nice to have
• Trying to go with a blue and white color scheme
Should not have
• Building construction

```html
<!DOCTYPE html>
<html lang="en">
<head>
<meta charset="utf-8">
<title>RK Wrecking – Business Card</title>
<link href="https://fonts.googleapis.com/css2?family=Open+Sans:wght@400;600;700;800&family=Oswald:wght@500;600&display=swap" rel="stylesheet">
<style>
  :root{
    --bg:#232323;
    --card-dark:#1c1c1f;
    --card-dark-2:#232327;
    --card-dark-3:#2b2b30;
    --brand-blue:#0c4fa3;
    --brand-blue-deep:#0b4490;
    --brand-blue-soft:#6e8fcb;
    --brand-blue-light:#7badd7;
    --text-light:#ffffff;
  }
  *{box-sizing:border-box;margin:0;padding:0}
  html,body{width:1200px;height:780px;overflow:hidden;background:var(--bg)}
  .stage{width:1200px;height:780px;display:flex;align-items:center;justify-content:center;gap:70px}
  .card{width:360px;height:630px;border-radius:22px;position:relative;overflow:hidden;box-shadow:0 14px 30px rgba(0,0,0,.55)}

  /* back side */
  .card--back{background:var(--brand-blue)}
  .back-pattern{position:absolute;inset:0;
    background:
      radial-gradient(ellipse 75% 55% at 0% 15%, rgba(150,175,225,.55) 0%, rgba(150,175,225,0) 70%),
      linear-gradient(160deg,var(--brand-blue-soft) 0%,#2a5eae 30%,var(--brand-blue) 55%,var(--brand-blue-deep) 100%)}
  .back-brand{position:absolute;top:44px;right:30px;display:flex;align-items:center;gap:8px;font-family:"Open Sans",sans-serif;font-weight:800;font-size:17px;color:var(--text-light)}
  .brand-dot{width:12px;height:12px;border-radius:50%;background:var(--text-light)}

  /* front side */
  .card--front{background:var(--card-dark-3);color:var(--text-light);font-family:"Open Sans",sans-serif;text-align:center}
  .front-curves{position:absolute;inset:0}
  .front-content{position:relative;z-index:1}
  .logo{display:flex;align-items:center;justify-content:center;gap:10px;margin-top:42px}
  .logo-dot{width:22px;height:22px;border-radius:50%;background:var(--brand-blue)}
  .logo-name{font-weight:800;font-size:30px;line-height:1.1;color:var(--text-light)}
  .license{font-family:"Oswald",sans-serif;font-weight:500;font-size:11px;letter-spacing:.5px;margin-top:4px}
  .credentials{font-family:"Oswald",sans-serif;font-weight:500;font-size:11px;letter-spacing:.8px;color:var(--brand-blue-light);margin-top:1px}
  .person-name{font-weight:800;font-size:27px;line-height:1.2;color:var(--brand-blue);margin-top:24px}
  .person-role{font-weight:600;font-size:14px;margin-top:2px}
  .icon-row{display:flex;justify-content:center;gap:10px;margin-top:10px}
  .icon{width:26px;height:26px;border-radius:50%;background:var(--brand-blue);display:flex;align-items:center;justify-content:center}
  .icon svg{width:14px;height:14px}
  .contact-lines{font-size:13px;line-height:1.45;margin-top:9px}
  .location{margin-top:10px;font-size:13px;line-height:1.4}
  .location .icon{margin:0 auto 5px}
  .services{position:absolute;left:0;right:0;bottom:34px;z-index:1}
  .services-title{font-weight:800;font-size:28px;line-height:1.2;color:var(--brand-blue)}
  .services-tagline{font-family:"Oswald",sans-serif;font-weight:500;font-size:12px;letter-spacing:-.2px;margin-top:2px}
  .services-list{list-style:none;font-size:13.5px;line-height:1.35;margin-top:6px}
</style>
</head>
<body>
<main class="stage">

  <section class="card card--back" aria-label="Card back">
    <div class="back-pattern" role="img" aria-label="Repeating brand pattern in blue tones"></div>
    <div class="back-brand"><span class="brand-dot"></span>RK Wrecking</div>
  </section>

  <section class="card card--front" aria-label="Card front">
    <svg class="front-curves" viewBox="0 0 360 630" preserveAspectRatio="none" aria-hidden="true">
      <path d="M0 0 H360 V630 H0 Z" fill="var(--card-dark-3)"/>
      <path d="M0 0 H360 V400 Q250 420 120 520 Q60 560 0 570 Z" fill="var(--card-dark-2)"/>
      <path d="M0 0 H360 V330 Q330 420 180 445 Q90 458 0 455 Z" fill="var(--card-dark)"/>
    </svg>

    <div class="front-content">
      <div class="logo"><span class="logo-dot"></span><span class="logo-name">RK Wrecking</span></div>
      <p class="license">LICENSE#4837215</p>
      <p class="credentials">LICENSED, BONDED, &amp; INSURED</p>

      <h1 class="person-name">Marcello Vandora</h1>
      <p class="person-role">Owner our city state and zip</p>

      <div class="icon-row">
        <span class="icon"><svg viewBox="0 0 24 24"><path fill="#fff" d="M6.6 10.8a15 15 0 0 0 6.6 6.6l2.2-2.2c.3-.3.7-.4 1-.2 1.1.4 2.3.6 3.6.6.6 0 1 .4 1 1V20c0 .6-.4 1-1 1A17 17 0 0 1 3 4c0-.6.4-1 1-1h3.5c.6 0 1 .4 1 1 0 1.3.2 2.5.6 3.6.1.3 0 .7-.2 1z"/></svg></span>
        <span class="icon"><svg viewBox="0 0 24 24"><rect x="3" y="6" width="18" height="12" rx="1.5" fill="none" stroke="#fff" stroke-width="2"/><path d="M3 7l9 6 9-6" fill="none" stroke="#fff" stroke-width="2"/></svg></span>
        <span class="icon"><svg viewBox="0 0 24 24"><circle cx="12" cy="12" r="9" fill="none" stroke="#fff" stroke-width="2"/><path d="M3 12h18M12 3c3 3 3 15 0 18M12 3c-3 3-3 15 0 18" fill="none" stroke="#fff" stroke-width="1.6"/></svg></span>
      </div>

      <p class="contact-lines">
        (555) 274-9136<br>
        info@brightlanecrews.com<br>
        Marcellov@brightlanecrews.com
      </p>

      <div class="location">
        <span class="icon"><svg viewBox="0 0 24 24"><path fill="#fff" d="M12 2a7 7 0 0 0-7 7c0 5 7 13 7 13s7-8 7-13a7 7 0 0 0-7-7zm0 9.5A2.5 2.5 0 1 1 12 6.5a2.5 2.5 0 0 1 0 5z"/></svg></span>
        Cedar Ridge Valley,<br>CA, 90000
      </div>
    </div>

    <div class="services">
      <h2 class="services-title">R Wrecking</h2>
      <p class="services-tagline">R WRECKING SELECTIVE DEMOLITION &amp; FULL DEMOLITION</p>
      <ul class="services-list">
        <li>Sheds</li>
        <li>Digging</li>
        <li>Kitchens</li>
        <li>Bathrooms</li>
        <li>AD Preparation</li>
        <li>Interiors &amp; Exteriors Demo</li>
      </ul>
    </div>
  </section>

</main>
</body>
</html>
```